VFX Company Business Card Design Project

The Kestrel Works is a decentralized Visual Effects Studio servicing the television and feature film industries.
Project Brief:
Take our logo that was previously designed on Pencil Harbor and make a double sided business card.
Requirements:
- Card MUST be double sided.
- Front of card MUST have the yellow part of our logo against the dark grey background.
- Back of card is completely up to the designer.
- Back of card must include the complete company logo.
Please follow these File Preparation guidelines:
http://printnook.ca/infopage?file=filetype_en&s=PrintNook_new&lang=en
Business

```html
<!DOCTYPE html>
<html lang="en">
<head>
<meta charset="utf-8">
<title>The Kestrel Works – Business Card Set</title>
<link rel="stylesheet" href="https://fonts.googleapis.com/css2?family=Jost:wght@400;500;600&family=Source+Sans+3:wght@400;600&display=swap">
<style>
  :root {
    --backdrop: #7a4426;
    --card-dark: #252525;
    --card-light: #e9efe4;
    --card-slate: #5f6b6d;
    --brand-yellow: #fbc52a;
    --ink-dark: #262626;
    --ink-light: #ffffff;
    --ink-soft: #e6e6e6;
    --rule: #bdbdbd;
  }
  * { box-sizing: border-box; margin: 0; padding: 0; }
  html, body { width: 1200px; height: 733px; overflow: hidden; }
  body {
    position: relative;
    background: var(--backdrop);
    font-family: "Source Sans 3", Arial, sans-serif;
  }
  .card {
    position: absolute;
    width: 524px;
    height: 298px;
    border-radius: 28px;
    overflow: hidden;
    box-shadow: 0 2px 6px rgba(0,0,0,0.35);
  }
  .card--front { left: 68px; top: 44px; background: var(--card-dark); }
  .card--contact { left: 630px; top: 48px; background: var(--card-dark); }
  .card--light { left: 66px; top: 385px; background: var(--card-light); }
  .card--slate { left: 624px; top: 389px; background: var(--card-slate); }

  .brand-name {
    position: absolute;
    font-family: "Jost", Arial, sans-serif;
    font-weight: 600;
    white-space: nowrap;
    letter-spacing: 0.5px;
  }
  .card--front .brand-name {
    left: 0; right: 0; top: 118px;
    text-align: center;
    font-size: 46px;
    color: var(--brand-yellow);
  }
  .card--contact .brand-name {
    left: 30px; top: 131px;
    font-size: 25px;
    color: var(--ink-soft);
  }
  .card--light .brand-name {
    left: 0; right: 0; top: 116px;
    text-align: center;
    font-size: 42px;
    color: var(--ink-dark);
  }
  .card--light .brand-dot {
    display: inline-block;
    width: 26px; height: 26px;
    border-radius: 50%;
    background: var(--ink-dark);
    margin-right: 14px;
    vertical-align: 2px;
  }
  .card--slate .brand-name {
    left: 0; right: 0; top: 104px;
    text-align: center;
    font-size: 52px;
    color: var(--ink-light);
  }

  .web-address {
    position: absolute;
    left: 0; right: 0;
    text-align: center;
    font-family: "Jost", Arial, sans-serif;
    font-weight: 500;
    font-size: 17px;
    letter-spacing: 3px;
  }
  .card--light .web-address { top: 254px; color: var(--ink-dark); }
  .card--slate .web-address { top: 256px; color: var(--ink-light); }

  .contact-rule {
    position: absolute;
    left: 300px; top: 52px;
    width: 2px; height: 195px;
    background: var(--rule);
  }
  .contact-rule::before {
    content: "";
    position: absolute;
    left: -1px; top: 0;
    width: 4px; height: 46px;
    background: var(--ink-light);
  }
  .person {
    position: absolute;
    left: 320px; top: 50px;
    color: var(--ink-light);
  }
  .person__name { font-size: 20px; font-weight: 600; line-height: 26px; }
  .person__title { font-size: 16px; line-height: 22px; color: var(--ink-soft); }

  .contact-list {
    position: absolute;
    left: 320px; top: 114px;
    list-style: none;
    color: var(--ink-soft);
    font-size: 14px;
  }
  .contact-list li {
    display: flex;
    align-items: flex-start;
    gap: 6px;
    line-height: 17px;
    height: 21px;
  }
  .contact-list li.contact-list__address { margin-top: 14px; height: auto; }
  .contact-list svg { width: 11px; height: 11px; flex: none; margin-top: 3px; fill: var(--ink-soft); }
</style>
</head>
<body>

  <section class="card card--front" aria-label="Card front">
    <span class="brand-name">The Kestrel Works</span>
  </section>

  <section class="card card--contact" aria-label="Card back, contact side">
    <span class="brand-name">The Kestrel Works</span>
    <div class="contact-rule"></div>
    <div class="person">
      <p class="person__name">Your Name</p>
      <p class="person__title">Title</p>
    </div>
    <ul class="contact-list">
      <li>
        <svg viewBox="0 0 12 12" aria-hidden="true"><path d="M3 1l2 2.5-1.2 1.3a7 7 0 0 0 3.4 3.4L8.5 7 11 9l-1.3 2C5 11 1 7 1 2.3z"/></svg>
        0987 654321
      </li>
      <li>
        <svg viewBox="0 0 12 12" aria-hidden="true"><rect x="3" y="0.5" width="6" height="11" rx="1.2"/><rect x="4" y="2" width="4" height="6.5" fill="#252525"/></svg>
        0987 654321
      </li>
      <li>
        <svg viewBox="0 0 12 12" aria-hidden="true"><path d="M1 2.5h10v7H1z"/><path d="M1 2.5l5 4 5-4" fill="none" stroke="#252525" stroke-width="1.2"/></svg>
        info@kestrelworks.com
      </li>
      <li>
        <svg viewBox="0 0 12 12" aria-hidden="true"><circle cx="6" cy="6" r="5" fill="none" stroke="#e6e6e6" stroke-width="1.2"/><path d="M1 6h10M6 1c-2.5 3-2.5 7 0 10M6 1c2.5 3 2.5 7 0 10" fill="none" stroke="#e6e6e6" stroke-width="1"/></svg>
        www.kestrelworks.com
      </li>
      <li class="contact-list__address">
        <svg viewBox="0 0 12 12" aria-hidden="true"><path d="M6 0.5a4 4 0 0 1 4 4c0 3-4 7-4 7s-4-4-4-7a4 4 0 0 1 4-4z"/><circle cx="6" cy="4.5" r="1.5" fill="#252525"/></svg>
        <span>00, Complex name<br>City, State 0042</span>
      </li>
    </ul>
  </section>

  <section class="card card--light" aria-label="Card back, light version">
    <span class="brand-name"><span class="brand-dot"></span>The Kestrel Works</span>
    <p class="web-address">www.kestrelworks.com</p>
  </section>

  <section class="card card--slate" aria-label="Card back, slate version">
    <span class="brand-name">The Kestrel Works</span>
    <p class="web-address">www.kestrelworks.com</p>
  </section>

</body>
</html>
```